Irrigation Business needs their business cards modernised and revamped

I would like to keep my current logo, colours and revamp the format of the card.

I would like the card to be clean yet important.

Im not sure if you include texture but i would like the named logo to be indented into the card etc.

show me something alive and free something thats clinical to the point yet has a feel of achievement. i would like people to go nice card.

Target Market(s)

high end clients, corporate, sports field manger, the guys that make the decisions

Industry/Entity Type

Business

Contact Information for Business Card

nformation to be included

Dean Harlow (Director)
0487305526
dean@kolvat.biz
www.kestonfieldworks.com

instagram logo
google logo
facebook logo

Colors

Designer to choose colors to be used in the design.

Requirements
Nice to have
• indentations a really nice feel to the card good texture

```html
<!DOCTYPE html>
<html lang="en">
<head>
<meta charset="utf-8">
<title>Keston Fieldworks — Business Card</title>
<link rel="stylesheet" href="https://fonts.googleapis.com/css2?family=Open+Sans:wght@400;600;700&display=swap">
<style>
  :root {
    --backdrop: #e6e8ea;
    --card: #f5f6f7;
    --card-edge: #dfe2e5;
    --brand-blue: #2f64ac;
    --disc-blue: #2fa6da;
    --ring-silver: #e3e7ea;
    --white: #ffffff;
  }
  * { margin: 0; padding: 0; box-sizing: border-box; }
  html, body {
    width: 1200px; height: 900px; overflow: hidden;
    background: var(--backdrop);
    font-family: "Open Sans", Arial, sans-serif;
  }
  .business-card {
    position: absolute; left: 150px; top: 173px;
    width: 900px; height: 554px;
    background: var(--card);
    border: 1px solid var(--card-edge);
    border-radius: 22px;
    box-shadow: 0 18px 40px rgba(40, 60, 80, 0.16);
    overflow: hidden;
  }
  .card-art { position: absolute; inset: 0; }
  .brand-name {
    position: absolute;
    left: 197px; top: 277px;
    transform: translate(-50%, -50%) rotate(-90deg);
    white-space: nowrap;
    font-weight: 700; font-size: 34px; letter-spacing: 0.5px;
    color: var(--brand-blue);
  }
  .contact-panel {
    position: absolute;
    left: 344px; top: 32px; width: 490px;
    text-align: center; color: var(--white);
  }
  .person-name { margin-top: 58px; font-weight: 700; font-size: 30px; line-height: 36px; }
  .person-role { font-size: 22px; line-height: 26px; }
  .contact-icons { display: flex; justify-content: center; gap: 8px; margin-top: 54px; height: 24px; }
  .contact-lines { margin-top: 12px; font-size: 23px; line-height: 32px; }
</style>
</head>
<body>
  <div class="business-card">
    <svg class="card-art" width="900" height="554" viewBox="0 0 900 554" aria-hidden="true">
      <!-- brand mark placeholder -->
      <circle cx="89" cy="277" r="41" fill="var(--brand-blue)"/>
      <!-- outer ring: solid upper arc -->
      <path d="M 326 340 A 271 271 0 1 1 852 340" fill="none" stroke="var(--brand-blue)" stroke-width="11"/>
      <!-- outer ring: broken lower segments -->
      <g fill="none" stroke="var(--brand-blue)" stroke-width="11">
        <path d="M 332 362 A 271 271 0 0 0 344 395"/>
        <path d="M 352 412 A 271 271 0 0 0 368 440"/>
        <path d="M 380 456 A 271 271 0 0 0 404 482"/>
        <path d="M 420 496 A 271 271 0 0 0 589 548"/>
        <path d="M 589 548 A 271 271 0 0 0 758 496"/>
        <path d="M 774 482 A 271 271 0 0 0 798 456"/>
        <path d="M 810 440 A 271 271 0 0 0 826 412"/>
        <path d="M 834 395 A 271 271 0 0 0 846 362"/>
      </g>
      <!-- silver inner ring -->
      <circle cx="589" cy="277" r="256" fill="var(--ring-silver)"/>
      <!-- main disc -->
      <circle cx="589" cy="277" r="245" fill="var(--disc-blue)"/>
      <!-- social placeholders -->
      <g fill="var(--ring-silver)">
        <circle cx="535" cy="451" r="22"/>
        <circle cx="591" cy="451" r="22"/>
        <circle cx="646" cy="451" r="22"/>
      </g>
    </svg>

    <div class="brand-name">KESTON FIELDWORKS</div>

    <div class="contact-panel">
      <div class="person-name">DEAN HARLOW</div>
      <div class="person-role">Director</div>
      <div class="contact-icons">
        <svg width="24" height="24" viewBox="0 0 24 24" aria-label="Phone">
          <circle cx="12" cy="12" r="12" fill="var(--white)"/>
          <path d="M8 7c1-1 2 0 2.5 1.5.3 1-.8 1.3-.5 2 .6 1.4 1.6 2.4 3 3 .7.3 1-.8 2-.5 1.5.5 2.5 1.5 1.5 2.5-2.5 2.5-10-5-8.5-8.5z" fill="var(--disc-blue)"/>
        </svg>
        <svg width="24" height="24" viewBox="0 0 24 24" aria-label="Email">
          <circle cx="12" cy="12" r="12" fill="var(--white)"/>
          <rect x="6" y="8" width="12" height="8" fill="var(--disc-blue)"/>
          <path d="M6 8l6 5 6-5" fill="none" stroke="var(--white)" stroke-width="1.2"/>
        </svg>
        <svg width="24" height="24" viewBox="0 0 24 24" aria-label="Website">
          <circle cx="12" cy="12" r="12" fill="var(--white)"/>
          <circle cx="12" cy="12" r="6" fill="none" stroke="var(--disc-blue)" stroke-width="1.6"/>
          <path d="M6 12h12M12 6c-3 3-3 9 0 12M12 6c3 3 3 9 0 12" fill="none" stroke="var(--disc-blue)" stroke-width="1.2"/>
        </svg>
      </div>
      <div class="contact-lines">
        <div>0487305526</div>
        <div>dean@kolvat.biz</div>
        <div>www.kestonfieldworks.com</div>
      </div>
    </div>
  </div>
</body>
</html>
```